VKT Consulting

Government/Entitlement Consulting Services- I assist developers obtain entitlements from local, state and federal government agencies so that they can build their projects. Often these projects are very complicated and political and may face community opposition.

Target Market(s)

Real Estate Developers

Industry/Entity Type

Business Consultant

Contact Information for Business Card

Dana Melbrook
Principal

Font styles to use
Serif
Sans Serif

Requirements
Must have
• Classy and professional appeal.
Nice to have
• I like a combination of a mat and glossy finish. I've seen that done with black and then a bold color for a pop, but am not 100% committed to that.

```html
<!DOCTYPE html>
<html lang="en">
<head>
<meta charset="utf-8">
<title>VKT Consulting – Business Card</title>
<link rel="stylesheet" href="https://fonts.googleapis.com/css2?family=Cinzel:wght@400&family=PT+Sans:wght@400;700&display=swap">
<style>
  :root {
    --backdrop: #121212;
    --card-light: #f3f3f3;
    --brand-blue: #1056b4;
    --ink-dark: #2a2a2a;
    --ink-grey: #555555;
    --white: #ffffff;
  }
  * { margin: 0; padding: 0; box-sizing: border-box; }
  html, body {
    width: 1200px;
    height: 900px;
    overflow: hidden;
    background: var(--backdrop);
  }
  .canvas {
    position: relative;
    width: 1200px;
    height: 900px;
  }
  .card {
    position: absolute;
    top: 184px;
    height: 490px;
    border-radius: 12px;
    text-align: center;
  }
  .card--front {
    left: 299px;
    width: 301px;
    background: var(--card-light);
  }
  .card--back {
    left: 645px;
    width: 305px;
    background: var(--brand-blue);
  }
  .wordmark {
    position: absolute;
    left: 0;
    right: 0;
    font-family: "Cinzel", serif;
    font-weight: 400;
    line-height: 1;
  }
  .wordmark__initials {
    display: block;
    font-size: 84px;
    letter-spacing: 2px;
  }
  .wordmark__descriptor {
    display: block;
    font-size: 26px;
    letter-spacing: 3px;
    margin-top: 8px;
  }
  .card--front .wordmark { top: 92px; color: var(--brand-blue); }
  .card--back .wordmark { top: 192px; color: var(--white); }
  .contact {
    position: absolute;
    top: 264px;
    left: 0;
    right: 0;
    font-family: "PT Sans", sans-serif;
    color: var(--ink-grey);
    font-size: 14px;
    line-height: 17.5px;
  }
  .contact__name {
    color: var(--brand-blue);
    font-weight: 700;
    font-size: 17px;
    line-height: 20px;
  }
  .contact__block { margin-top: 13px; }
</style>
</head>
<body>
<main class="canvas">
  <section class="card card--front" aria-label="Business card front">
    <div class="wordmark">
      <span class="wordmark__initials">VKT</span>
      <span class="wordmark__descriptor">CONSULTING</span>
    </div>
    <div class="contact">
      <p class="contact__name">Dana Melbrook</p>
      <p class="contact__title">Principal</p>
      <p class="contact__block">48 Harbor Lane, Suite 210<br>Westfield County, 204518.</p>
      <p class="contact__block">044-555 018 274<br>info@vktconsult.com<br>www.vktconsult.com</p>
    </div>
  </section>
  <section class="card card--back" aria-label="Business card back">
    <div class="wordmark">
      <span class="wordmark__initials">VKT</span>
      <span class="wordmark__descriptor">CONSULTING</span>
    </div>
  </section>
</main>
</body>
</html>
```